Form With Marla - Health and Wellness Business Card and Logo

I need a business card design with a logo for my business you can check out at www.formwithmarla.net. I want something more original, simplistic, and memorable than the basic logo I have on my site currently. I am a health and wellness coach and I offer mindset coaching and nutrition plans. I like the colour teal and dark grey/black for my theme colours. I emphasize growth, longterm change, and the whole package of "healthy mind, healthy body, healthy life". I had played around the idea of intertwining 3 M's or incorporating growth (leaves etc.) into my design. I want my expertise and experience to show through. In one glance I want people to understand with confidence I can help them accomplish anything they set their minds to. I look forward to seeing what everyone comes up with!

Industry/Entity Type

Health And Wellness

Contact Information for Business Card

Form With Marla
Marla Prentiss
BSc, Health & Wellness Coach
"Manifest your best"
www.formwithmarla.net
formwithmarla@quillpost.net
472-618-9043

Colors
33b8a4
ffffff
333333
000000

Requirements
Must have
• A memorable and unique logo for my business!
Nice to have
• Could have the phrase "Are you unhappy with your body and state of health?" or "It takes the right skills to develop habits in order to create long term change. I can help you get there."

```html
<!DOCTYPE html>
<html lang="en">
<head>
<meta charset="utf-8">
<title>Form With Marla – Business Card</title>
<link rel="stylesheet" href="https://fonts.googleapis.com/css2?family=Didact+Gothic&family=Open+Sans:wght@400;700&display=swap">
<style>
  :root {
    --backdrop: #2b2b2b;
    --card-dark: #1e1e1e;
    --card-light: #ffffff;
    --ink: #333333;
    --ink-soft: #555555;
    --mark-dark: #bdbdbd;
    --tagline: #d8d8d8;
    --tab: #333333;
  }
  * { box-sizing: border-box; margin: 0; padding: 0; }
  html, body { width: 1200px; height: 1000px; overflow: hidden; }
  body {
    background: var(--backdrop);
    position: relative;
    font-family: "Open Sans", sans-serif;
  }
  .card {
    position: absolute;
    left: 250px;
    width: 700px;
    height: 400px;
    border-radius: 4px;
    overflow: hidden;
  }
  /* front */
  .card--front { top: 50px; background: var(--card-dark); }
  .front__mark {
    position: absolute;
    top: 140px; left: 0; width: 100%;
    text-align: center;
    font-family: "Didact Gothic", sans-serif;
    font-size: 46px;
    color: var(--mark-dark);
  }
  .front__tagline {
    position: absolute;
    bottom: 50px; left: 0; width: 100%;
    text-align: center;
    font-size: 15px;
    letter-spacing: 6px;
    color: var(--tagline);
  }
  /* back */
  .card--back { top: 510px; background: var(--card-light); }
  .back__wordmark {
    position: absolute;
    top: 42px; left: 50px;
    font-family: "Didact Gothic", sans-serif;
    font-size: 50px;
    color: var(--ink);
  }
  .back__tab {
    position: absolute;
    top: 135px; left: 0;
    width: 12px; height: 40px;
    background: var(--tab);
    border-radius: 0 4px 4px 0;
  }
  .person { position: absolute; top: 132px; left: 44px; color: var(--ink); }
  .person__name { font-size: 27px; font-weight: 700; line-height: 1.1; }
  .person__role { font-size: 14px; font-weight: 700; color: var(--ink-soft); }
  .contact {
    position: absolute; top: 215px; left: 40px;
    list-style: none;
    font-size: 18px; color: var(--ink-soft);
  }
  .contact li { display: flex; align-items: center; height: 24px; }
  .contact svg { width: 14px; height: 14px; margin-right: 14px; fill: var(--ink); }
  .contact strong { font-weight: 700; color: var(--ink); }
  .back__mark {
    position: absolute; right: 40px; bottom: 38px;
    font-size: 22px; font-weight: 700; color: var(--ink);
  }
</style>
</head>
<body>
  <section class="card card--front">
    <div class="front__mark">form with marla</div>
    <p class="front__tagline">"Manifest your best"</p>
  </section>

  <section class="card card--back">
    <div class="back__wordmark">form with marla</div>
    <div class="back__tab"></div>
    <div class="person">
      <h1 class="person__name">MARLA PRENTISS</h1>
      <p class="person__role">BSc, Health &amp; Wellness Coach</p>
    </div>
    <ul class="contact">
      <li><svg viewBox="0 0 24 24"><path d="M6.6 10.8a15 15 0 0 0 6.6 6.6l2.2-2.2c.3-.3.7-.4 1-.2 1.1.4 2.3.6 3.6.6.6 0 1 .4 1 1V20c0 .6-.4 1-1 1A17 17 0 0 1 3 4c0-.6.4-1 1-1h3.5c.6 0 1 .4 1 1 0 1.3.2 2.5.6 3.6.1.3 0 .7-.2 1z"/></svg>472-618-9043</li>
      <li><svg viewBox="0 0 24 24"><path d="M2 5h20v14H2z M2 5l10 8 10-8" fill="none" stroke="#333" stroke-width="2.5"/></svg>formwithmarla@quillpost.net</li>
      <li><svg viewBox="0 0 24 24"><circle cx="12" cy="12" r="10" fill="none" stroke="#333" stroke-width="2"/><path d="M2 12h20M12 2c3 3 3 17 0 20M12 2c-3 3-3 17 0 20" fill="none" stroke="#333" stroke-width="2"/></svg>www.<strong>formwithmarla</strong>.net</li>
      <li><svg viewBox="0 0 24 24"><rect x="3" y="3" width="18" height="18" rx="4"/></svg>@marlaprentiss</li>
    </ul>
    <div class="back__mark">Form With Marla</div>
  </section>
</body>
</html>
```